Useable Postcard Gift for Artistic Convention Use

Useable Postcard Gift Conference Use, search for web designers
Name of the Company is: Verdancy Harbor
I have an image that I would like to use for the front of the card
along with a by line which says "Let Each Step Light the Road Ahead"
Regarding image, i am good to leave the black behind.... should the designer choose. I also have a black and white image to use as well if someone needs it.

Design Target Market: State of the Art, Hip, Elegant, Conscious

This card will be used at a state of the art tech Quorvel Summit in Los Angeles. We want to hand it out to those we are interested in continuing relationship with for the purpose of building a website that is comprehensive. We are looking for designers and tech builders for the site.

This is a service business. I would like to have 3 names and titles on the back of the card and a small paragraph of copy. I like the beauty of the postcard i have saved on my account. I like Copper Gothic, thin lettering and Amazone or Caligraphy where it fits.... if it fits.

I want the card to communicate interest in Verdancy Harbor as a state of the art web community that services those progressive professionals who are interested in personal balance and who want to purchase products that are essential to a healthful life.
Updates

Project Deadline Extended
Reason: The deadline is extended through tomorrow due to the need to complete a design. Please continue support

Target Market(s)

High profile clients for coaching, web designers and web technicians for elaborate website build.

Industry/Entity Type

Progressive

Font styles to use
Serif
Script

Colors
00a88f
0555a3
6b449b
ffc214
9bcb3b
f37022

Requirements
Nice to have
• This was supposed to be the must have feature but it wouldn't return there so-----
We want the card to be elegant and definitely a useable postcard.

```html
<!DOCTYPE html>
<html lang="en">
<head>
<meta charset="utf-8">
<title>Verdancy Harbor Postcard Back</title>
<link rel="stylesheet" href="https://fonts.googleapis.com/css2?family=Cinzel:wght@400;500&family=Roboto+Condensed:wght@300&family=Arimo:wght@700&display=swap">
<style>
  :root {
    --ink: #000000;
    --paper: #ffffff;
    --panel-top: #ffffff;
    --panel-bottom: #d3d9d9;
    --tab-face: #fbfbfb;
    --tab-edge: #8a857a;
    --text: #2b2b2b;
  }
  * { margin: 0; padding: 0; box-sizing: border-box; }
  html, body { width: 1200px; height: 923px; overflow: hidden; background: var(--paper); }
  .postcard { position: relative; width: 1200px; height: 923px; background: var(--paper); }
  .panel-shape { position: absolute; left: 0; top: 0; }
  .brand-name {
    position: absolute; left: 52px; top: 22px;
    font-family: "Cinzel", serif; font-weight: 500; font-size: 38px;
    color: var(--paper); letter-spacing: 1px; white-space: nowrap;
  }
  .name-tab {
    position: absolute; width: 365px; height: 70px;
    background: linear-gradient(var(--tab-face), #f2f2f2);
    border-left: 2px solid var(--tab-edge); border-right: 2px solid var(--tab-edge);
    box-shadow: 0 10px 12px -6px rgba(0,0,0,0.35);
    display: flex; align-items: center; justify-content: center;
    font-family: "Cinzel", serif; font-size: 34px; color: var(--ink);
  }
  .name-tab--one { left: 175px; top: 98px; }
  .name-tab--two { left: 125px; top: 192px; }
  .name-tab--three { left: 45px; top: 284px; }
  .about {
    position: absolute; left: 33px; top: 393px; width: 513px;
    font-family: "Roboto Condensed", sans-serif; font-weight: 300;
    font-size: 27px; line-height: 38.5px; color: var(--text);
    text-align: justify;
  }
  .about p { text-indent: 77px; }
  .postage {
    position: absolute; left: 975px; top: 75px; width: 140px; height: 140px;
    border: 2px solid var(--ink);
    display: flex; align-items: center; justify-content: center; text-align: center;
    font-family: "Arimo", sans-serif; font-weight: 700; font-size: 26px; line-height: 32px;
    color: var(--ink); padding-bottom: 12px;
  }
  .address-line {
    position: absolute; left: 695px; width: 406px; height: 0;
    border-top: 3px solid var(--ink);
  }
</style>
</head>
<body>
<main class="postcard">
  <svg class="panel-shape" width="1200" height="923" viewBox="0 0 1200 923" aria-hidden="true">
    <defs>
      <linearGradient id="panelFade" x1="0" y1="0" x2="0" y2="1">
        <stop offset="0" stop-color="var(--panel-top)"/>
        <stop offset="1" stop-color="var(--panel-bottom)"/>
      </linearGradient>
    </defs>
    <path d="M0 0 H572 V742 H190 C160 742 150 760 130 772 C118 780 110 782 100 782 H0 Z" fill="url(#panelFade)"/>
    <path d="M190 742 C160 742 150 760 130 772 C118 780 110 782 100 782 H0" fill="none" stroke="var(--ink)" stroke-width="3"/>
    <path d="M0 0 H572 V74 H188 C160 74 150 90 135 102 C125 110 118 115 105 115 H0 Z" fill="var(--ink)"/>
    <rect x="571" y="0" width="7" height="744" fill="var(--ink)"/>
  </svg>

  <div class="brand-name">Verdancy Harbor</div>

  <div class="name-tab name-tab--one">Name - 1</div>
  <div class="name-tab name-tab--two">Name - 2</div>
  <div class="name-tab name-tab--three">Name - 3</div>

  <div class="about">
    <p>Verdancy Harbor is a state of the art web community that services those progressive professionals who are interested in personal balance and who want to purchase products that are essential to a healthful life.</p>
    <p>Your text goes here.Your text goes here. Your text goes here. Your text goes here. Your text goes here.</p>
  </div>

  <div class="postage">Postage<br>Area</div>

  <div class="address-line" style="top: 440px;"></div>
  <div class="address-line" style="top: 511px;"></div>
  <div class="address-line" style="top: 581px;"></div>
  <div class="address-line" style="top: 653px;"></div>
</main>
</body>
</html>
```